Wordpress Web Design & Coding for velcorahealth.ca

We need a website for a new investment company that is visually grabbing and vibrant. We would like to see a web page that displays trust, growth and confidence. Needs to be responsive and mobile friendly for all browsers and coded for both Android & IOS.

Open to the number of pages and menu items. I selected 4 but if you feel the layout would work better with less I am open to this. Need to sell the people (management team/related businesses) and then show where the invested money will be going (upcoming projects).

Company Info:

Vel Cora is an investment company put together by a group of seasoned business professionals who have come together to combine decades of success in the real estate development, management, financing and medical services. The company will be a full service company offering turn key solutions for medical professionals.

Vel-Cora will focus on providing a full range of services via a group of distinct companies to deliver newly emerging needs of the medical community. The end goal will be to create complete solutions for individuals in the medical community. Our group has experience and success with the conceptualization, construction and financing of medical and dental clinic spaces. Vel-Cora Solutions will be established to accommodate all areas of the development and creation of clinics for medical professionals from building construction to equipment financing and administrations.

You can mention these companies and take photos from their websites. You can also use stock photos.

Our construction partner:
https://318bld.com/projects/

Our equipment leasing partner:
https://www.norvixa.com/

Our Management Team and medical partners

Gil Parish
https://www.ourfirmstance.ca/

Dietmar Vellasquin
https://www.gshdentalservices.com/about-us

PROPOSED PROJECTS (see attachment for details)
Pinegrove Business Park
Holtmere Business Park
Mt. Corwin Ridge Professional

Target Market(s)

Investors

Industry/Entity Type

Investment

Coding

Coded - Design and coding required

Number of Pages Required

4 page

Font styles to use
Sans Serif

Requirements
Must have
• Wordpress – must be both desktop and mobile friendly with fast page load speed
Ability to edit after ourselves in Wordpress
Attractive home page with logo etc.
Logo colours are: for the blue the pantone color is #0355a3
and for the green is #8cc63f

Sections, about us, what we do/services we provide, contact us

```html
<!DOCTYPE html>
<html lang="en">
<head>
<meta charset="utf-8">
<title>Vel-Cora Solutions</title>
<link href="https://fonts.googleapis.com/css2?family=Montserrat:wght@400;500;600;700&display=swap" rel="stylesheet">
<style>
:root{
  --blue:#0355a3;
  --navy:#0b3a8c;
  --green:#7dbf35;
  --grey:#efefef;
  --text:#3a3a3a;
  --dark:#07142b;
  --white:#fff;
}
*{box-sizing:border-box;margin:0;padding:0}
html,body{width:1200px;height:3686px;overflow:hidden}
body{font-family:'Montserrat',sans-serif;color:var(--text);background:var(--white);position:relative}
.abs{position:absolute}
.btn{position:absolute;background:var(--navy);color:var(--white);font-weight:600;font-size:16px;display:flex;align-items:center;justify-content:center;letter-spacing:.3px}
.section-title{position:absolute;left:0;width:1200px;text-align:center;color:var(--green);font-weight:600;font-size:33px}

/* header */
.brand{left:144px;top:62px;display:flex;align-items:center;gap:12px}
.brand-mark{width:26px;height:26px;background:var(--green)}
.brand-name{font-size:30px;font-weight:700;color:var(--blue);line-height:1}
.email{right:145px;top:36px;font-size:20px;font-weight:500;color:#222;display:flex;align-items:center;gap:10px}
.nav{top:96px;font-size:15px;color:#444;letter-spacing:.2px}
.nav.active{color:var(--blue)}

/* hero */
.hero{left:0;top:168px;width:1200px;height:660px}
.hero-title{top:340px;left:0;width:1200px;text-align:center;color:var(--white);font-weight:700;font-size:32px;line-height:45px;text-shadow:0 2px 6px rgba(0,0,0,.4)}
.arrow{font-size:34px;color:var(--white)}

/* welcome */
.welcome-frame{left:144px;top:900px;width:432px;height:312px;background:var(--green)}
.welcome-photo{left:152px;top:900px;width:432px;height:304px;background:linear-gradient(135deg,#c98a4a 0%,#e8e1d8 45%,#3d4a63 100%)}
.welcome-title{left:614px;top:893px;font-size:33px;font-weight:600;color:var(--green)}
.welcome-text{left:614px;top:955px;width:445px;font-size:14.5px;line-height:30.4px;color:#333}

/* services */
.services-bg{left:0;top:1293px;width:1200px;height:460px;background:var(--grey)}
.card{top:1420px;width:297px;height:298px;background:var(--white);box-shadow:0 1px 6px rgba(0,0,0,.12);text-align:center}
.card svg{position:absolute;left:114px;top:36px}
.card h3{position:absolute;top:120px;width:100%;font-size:20px;font-weight:500;color:#222}
.card p{position:absolute;top:153px;left:22px;width:253px;font-size:10.5px;line-height:19px;color:#555}

/* industries */
.tile{top:2075px;width:217px;height:217px}
.tile span{position:absolute;bottom:10px;width:100%;text-align:center;color:var(--green);font-size:19px;font-weight:500}

/* partners */
.partners-bg{left:0;top:2372px;width:1200px;height:370px;background:var(--grey)}
.partner{top:2508px;width:217px;height:160px;background:var(--white)}
.partner-name{font-weight:700;font-size:14px;color:#1a237e;text-align:center;width:100%;position:absolute;top:70px}
.partner-photo{top:2508px;width:217px;height:160px}
.caption{top:2680px;width:217px;text-align:center;font-size:13px;color:#222}
.sub{top:2701px;width:217px;text-align:center;font-size:9.5px;color:#444}
.parrow{font-size:34px;color:#888}

/* contact */
.field{border:1px solid #bbb;background:var(--white);font-size:11px;color:#666;padding:14px 15px}

/* footer */
.foot-links{left:144px;top:3596px;font-size:11.5px;color:#8fa3c7;word-spacing:3px}
.foot-copy{left:144px;top:3629px;font-size:11.5px;color:#8fa3c7}
.foot-brand{left:890px;top:3498px;font-size:28px;font-weight:700;color:#2c4472;display:flex;align-items:center;gap:10px}
.foot-brand i{width:22px;height:22px;background:#2c4472;display:block}
.social{top:3604px;width:20px;height:20px;border-radius:50%;background:#5b6f94}
</style>
</head>
<body>

<!-- header -->
<div class="abs brand"><span class="brand-mark"></span><span class="brand-name">Vel-Cora Solutions</span></div>
<div class="abs email">
  <svg width="20" height="15" viewBox="0 0 20 15"><rect x="0" y="0" width="20" height="15" rx="1" fill="#222"/><path d="M1 1l9 7 9-7" stroke="#fff" stroke-width="1.6" fill="none"/></svg>
  info@velcorahealth.ca
</div>
<div class="abs nav active" style="left:542px">HOME</div>
<div class="abs nav" style="left:626px">SERVICES</div>
<div class="abs nav" style="left:734px">PARTNERS</div>
<div class="abs nav" style="left:850px">ABOUT US</div>
<div class="abs nav" style="left:963px">CONTACT US</div>

<!-- hero -->
<svg class="abs hero" viewBox="0 0 1200 660" role="img" aria-label="Business people reviewing financial charts on a laptop">
  <defs>
    <linearGradient id="heroGrad" x1="0" y1="0" x2="1" y2="1">
      <stop offset="0" stop-color="#6b7480"/>
      <stop offset=".5" stop-color="#8a929a"/>
      <stop offset="1" stop-color="#3e4650"/>
    </linearGradient>
  </defs>
  <rect width="1200" height="660" fill="url(#heroGrad)"/>
  <polygon points="0,452 275,652 1200,447 1200,660 0,660" fill="#fff"/>
  <polyline points="0,452 275,652 1200,447" fill="none" stroke="var(--green)" stroke-width="10"/>
</svg>
<div class="abs hero-title">PELLENTESQUE CONVALLIS MOLESTIE<br>ENIM AMET EFFICITUR</div>
<div class="btn" style="left:532px;top:442px;width:136px;height:44px">READ MORE</div>
<div class="abs arrow" style="left:58px;top:375px">&#8249;</div>
<div class="abs arrow" style="left:1120px;top:375px">&#8250;</div>

<!-- welcome -->
<div class="abs welcome-frame"></div>
<div class="abs welcome-photo" role="img" aria-label="Person using a tablet beside a laptop and printed charts"></div>
<div class="abs welcome-title">Welcome to Vel Cora</div>
<p class="abs welcome-text">Vel Cora is an investment company put together by a group of seasoned business professionals who have come together to combine decades of success in the real estate development, management, financing and medical services. The company will be a full service company offering turn key solutions for medical professionals.</p>
<div class="btn" style="left:614px;top:1160px;width:136px;height:44px">READ MORE</div>

<!-- services -->
<div class="abs services-bg"></div>
<svg class="abs" style="left:0;top:1740px" width="1200" height="210" viewBox="0 0 1200 210">
  <polygon points="0,0 1200,0 1200,5 922,200 0,5" fill="var(--grey)"/>
  <polyline points="0,5 922,200 1200,5" fill="none" stroke="var(--green)" stroke-width="9"/>
</svg>
<div class="section-title" style="top:1365px">Services</div>

<div class="abs card" style="left:144px">
  <svg width="70" height="70" viewBox="0 0 70 70" fill="none" stroke="#222" stroke-width="2"><rect x="10" y="8" width="46" height="58"/><rect x="16" y="3" width="46" height="58" fill="#fff"/><circle cx="34" cy="30" r="10"/><path d="M34 20v10h10"/><line x1="22" y1="48" x2="56" y2="48"/><line x1="22" y1="54" x2="50" y2="54"/></svg>
  <h3>Vestibulum</h3>
  <p>hasellus nisl condimentum faucibus sollicitudin vel metus. Nunc sit amet consequat risus. Curabitur ac elit leo. In eleifend dui tellus.</p>
  <div class="btn" style="left:81px;top:220px;width:136px;height:44px">READ MORE</div>
</div>
<div class="abs card" style="left:451px">
  <svg width="70" height="70" viewBox="0 0 70 70" fill="none" stroke="#222" stroke-width="2"><rect x="28" y="4" width="34" height="58"/><circle cx="45" cy="33" r="8"/><rect x="4" y="40" width="12" height="24"/><path d="M16 44h18l6 6v10H16"/></svg>
  <h3>Aenean sed</h3>
  <p>hasellus nisl condimentum faucibus sollicitudin vel metus. Nunc sit amet consequat risus. Curabitur ac elit leo. In eleifend dui tellus.</p>
  <div class="btn" style="left:81px;top:220px;width:136px;height:44px">READ MORE</div>
</div>
<div class="abs card" style="left:757px">
  <svg width="70" height="70" viewBox="0 0 70 70" fill="none" stroke="#222" stroke-width="2"><circle cx="35" cy="35" r="30"/><line x1="35" y1="5" x2="35" y2="65"/><line x1="5" y1="35" x2="65" y2="35"/><circle cx="50" cy="50" r="8"/><line x1="14" y1="52" x2="24" y2="42"/><rect x="12" y="14" width="4" height="14"/><rect x="19" y="18" width="4" height="10"/><rect x="26" y="10" width="4" height="18"/></svg>
  <h3>Praesent</h3>
  <p>hasellus nisl condimentum faucibus sollicitudin vel metus. Nunc sit amet consequat risus. Curabitur ac elit leo. In eleifend dui tellus.</p>
  <div class="btn" style="left:81px;top:220px;width:136px;height:44px">READ MORE</div>
</div>

<!-- industries -->
<div class="section-title" style="top:2018px">Industries</div>
<div class="abs tile" style="left:144px;background:linear-gradient(180deg,#b9c8da,#6c6660)" role="img" aria-label="Building under construction with a crane"><span>Construction</span></div>
<div class="abs tile" style="left:375px;background:linear-gradient(160deg,#f1e6de,#b7aca4 70%,#3a3a3a)" role="img" aria-label="Hands working with a calculator and papers"><span>Medical Solution</span></div>
<div class="abs tile" style="left:606px;background:linear-gradient(180deg,#6f91c7,#d8d8d8 55%,#1f2a38)" role="img" aria-label="Modern white house at dusk"><span>Real Estate</span></div>
<div class="abs tile" style="left:837px;background:linear-gradient(180deg,#a7c3de,#5c7391 60%,#233447)" role="img" aria-label="Stacks of coins with a rising chart"><span>Financing</span></div>

<!-- partners -->
<div class="abs partners-bg"></div>
<svg class="abs" style="left:0;top:2730px" width="1200" height="215" viewBox="0 0 1200 215">
  <polygon points="0,0 1200,0 1200,8 275,205 0,8" fill="var(--grey)"/>
  <polyline points="0,8 275,205 1200,8" fill="none" stroke="var(--green)" stroke-width="9"/>
</svg>
<div class="section-title" style="top:2444px">Partners</div>
<div class="abs parrow" style="left:58px;top:2565px">&#8249;</div>
<div class="abs parrow" style="left:1120px;top:2565px">&#8250;</div>

<div class="abs partner" style="left:144px"><div class="partner-name">318 BUILDERS INC.</div></div>
<div class="abs partner" style="left:375px"><div class="partner-name" style="color:#8a2b2b;font-weight:500;letter-spacing:3px;font-size:15px">NORVIXA</div></div>
<div class="abs partner-photo" style="left:606px;background:linear-gradient(180deg,#555,#7a6a60 60%,#2f2f2f)" role="img" aria-label="Portrait of Gil Parish"></div>
<div class="abs partner-photo" style="left:837px;background:linear-gradient(180deg,#c9d7e3,#6ea3b8 55%,#2b5c73)" role="img" aria-label="Portrait of Dietmar Vellasquin outdoors"></div>

<div class="abs caption" style="left:144px">Construction Partner</div>
<div class="abs caption" style="left:375px">Equipment Leasing Partner</div>
<div class="abs caption" style="left:606px">Gil Parish</div>
<div class="abs sub" style="left:606px">Management Team and medical partners</div>
<div class="abs caption" style="left:837px">Dietmar Vellasquin</div>
<div class="abs sub" style="left:837px">Management Team and medical partners</div>

<!-- contact -->
<div class="section-title" style="top:3010px">Contact Us</div>
<div class="abs field" style="left:144px;top:3067px;width:217px;height:40px">Name</div>
<div class="abs field" style="left:375px;top:3067px;width:217px;height:40px">Company Name</div>
<div class="abs field" style="left:606px;top:3067px;width:217px;height:40px">Email</div>
<div class="abs field" style="left:837px;top:3067px;width:218px;height:40px">Phone</div>
<div class="abs field" style="left:144px;top:3125px;width:911px;height:112px">Message</div>
<div class="btn" style="left:548px;top:3257px;width:104px;height:44px">SUBMIT</div>

<!-- footer -->
<svg class="abs" style="left:0;top:3378px" width="1200" height="308" viewBox="0 0 1200 308">
  <polygon points="0,202 922,6 1200,160 1200,308 0,308" fill="var(--dark)"/>
  <polyline points="0,202 922,6 1200,160" fill="none" stroke="var(--green)" stroke-width="9"/>
</svg>
<div class="abs foot-brand"><i></i>Vel-Cora</div>
<div class="abs foot-links">Home &nbsp;| &nbsp;Services &nbsp;| &nbsp;Partners &nbsp;| &nbsp;About Us &nbsp;| &nbsp;Contact Us</div>
<div class="abs foot-copy">Copyright © 2020 &nbsp;Vel Cora Solutions. &nbsp;All rights reserved.</div>
<div class="abs social" style="left:940px"></div>
<div class="abs social" style="left:992px"></div>

</body>
</html>
```